Business Card & Letterhead Design

We a financial advice company based in Australia. We provide advice to wealthy farmers.

We are changing our business name FROM Brightvale Financial TO Quellbrook Wealth and we need a new letterhead and double sided business card design

Attached is designs from our previous branding (Brightvale Financial) as it includes all the details we require on the new Quellbrook Wealth business cards and letterhead.

Need extra days to review

```html
<!DOCTYPE html>
<html lang="en">
<head>
<meta charset="utf-8">
<title>Quellbrook Wealth – Business Card Back</title>
<link rel="stylesheet" href="https://fonts.googleapis.com/css2?family=Smokum&family=Oswald:wght@400&display=swap">
<style>
  :root {
    --ink: #0a0a0a;
    --paper: #ffffff;
  }
  html, body {
    margin: 0;
    padding: 0;
    width: 1200px;
    height: 686px;
    overflow: hidden;
    background: var(--paper);
  }
  .card {
    position: relative;
    width: 1200px;
    height: 686px;
    background: var(--paper);
    color: var(--ink);
    font-family: "Smokum", "Oswald", sans-serif;
    font-variant: small-caps;
  }
  .card-frame {
    position: absolute;
    left: 23px;
    top: 25px;
    width: 1138px;
    height: 620px;
    border: 8px solid var(--ink);
    box-sizing: content-box;
  }
  .brand {
    position: absolute;
    left: 0;
    right: 0;
    top: 128px;
    height: 56px;
    display: flex;
    justify-content: center;
    align-items: center;
    gap: 16px;
  }
  .brand-dot {
    width: 30px;
    height: 30px;
    border: 4px solid var(--ink);
    border-radius: 50%;
    box-sizing: border-box;
  }
  .brand-name {
    font-size: 52px;
    line-height: 56px;
    white-space: nowrap;
  }
  .services {
    position: absolute;
    left: 0;
    right: 0;
    top: 262px;
    margin: 0;
    padding: 0;
    list-style: none;
    text-align: center;
    font-size: 44px;
    line-height: 51px;
    white-space: nowrap;
  }
  .licensee {
    position: absolute;
    left: 0;
    right: 0;
    top: 518px;
    text-align: center;
    font-size: 31px;
    line-height: 40px;
    white-space: nowrap;
  }
  .licensee p { margin: 0; }
</style>
</head>
<body>
  <div class="card">
    <div class="card-frame"></div>

    <div class="brand">
      <span class="brand-dot"></span>
      <span class="brand-name">Quellbrook Wealth</span>
    </div>

    <ul class="services">
      <li>Life &amp; TPD Insurance</li>
      <li>Income Protection</li>
      <li>Financial Planning</li>
      <li>Retirement Planning</li>
    </ul>

    <div class="licensee">
      <p>Meridian Advice Licensee Limited</p>
      <p>Australian Financial Services License Number 418207</p>
    </div>
  </div>
</body>
</html>
```